Brightwell Aero Services Logo

I need a website and logo for the parent company Brightwell Aero Services, which encompasses general aviation aircraft repair, small aircrat rental and flight school. The company is based in Lawrenceville, Georgia at the Tolleson county airport. A saying that can be incorporated somehere could be, "Quality flying is safe flying", "Safety in mind is no accident" ,. I need a website and logo.

The company started as a repair shop performing repairs and inspections on Harlan, Vantor, Delkin and Ralstead general aviation aircraft, all models of single engine piston, multi engine piston, and single engine turboprop with an emphasis on Harlan Solvane and AeroTurn turbo prop aircraft. We have se=ince entered the aircraft rental and flight instruction market using the Delkin 240 ang Harlan Ranger aircraft.

Number of Pages; I don't know. Maybe 5 ? A home page for Brightwell Aero Services, page for maintenance and repairs and a couple for the rental and school. The maintenance shop is busy, always has been. I need to get the rental and school advertised and busy.

I have a logo for the maintenance shop shirts, not for the school. I do not have the file. I paid a business locally to do that and print on the shirts. They have the file.

Target Market(s)

In our flight school rental fleet department, we are looking for persons wishing to obtain their private pilot license and continuing on into their commercial and instrument ratings. In the aircraft maintenance department, we are looking for new customers who want a better and more quality relationship with their aircraft maintenance provider who will give more detail and quality in the repairs with an emphasis on safety and fewer problems between scheduled maintenance cycles on their aircraft. Brightwell's owner, Dale Hutchins, has been performing aircraft maintenance in the Atlanta area for 27 years. He has built a steady customer base through those years.

```html
<!DOCTYPE html>
<html lang="en">
<head>
<meta charset="utf-8">
<title>Brightwell Aero Services</title>
<link href="https://fonts.googleapis.com/css2?family=Cabin:wght@500;600&family=Lato:wght@400&family=Poppins:wght@400;500&display=swap" rel="stylesheet">
<style>
:root{
  --header:#71b8c5;
  --accent:#2aa8b8;
  --card:#e3f2f4;
  --ink:#111111;
  --body:#555555;
  --footer:#000000;
  --white:#ffffff;
}
*{margin:0;padding:0;box-sizing:border-box}
html,body{width:1200px;height:3104px;overflow:hidden;background:var(--white)}
.page{position:relative;width:1200px;height:3104px;font-family:"Lato",sans-serif;color:var(--ink)}
.abs{position:absolute}
.site-header{left:0;top:0;width:1200px;height:95px;background:var(--header)}
.brand{display:flex;align-items:center;gap:18px;color:var(--white);font-family:"Cabin",sans-serif;font-weight:600;font-size:28px;line-height:30px;text-align:center}
.brand-mark{width:52px;height:52px;border:3px solid var(--white);border-radius:50%}
.nav{left:729px;top:40px;display:flex;gap:27px;font-family:"Cabin",sans-serif;font-size:17px;color:var(--white)}
.hero{left:0;top:95px;width:1200px;height:503px;background:linear-gradient(180deg,#2d3a4a 0%,#5a5f66 40%,#8a6a4c 70%,#3b3228 100%)}
.hero h1{left:114px;top:190px;font-family:"Cabin",sans-serif;font-weight:600;font-size:54px;line-height:52px;color:var(--white)}
.btn{display:flex;align-items:center;justify-content:center;width:134px;height:50px;background:var(--accent);color:var(--white);font-family:"Lato",sans-serif;font-size:17px}
.section-title{left:0;width:1200px;text-align:center;font-family:"Cabin",sans-serif;font-weight:500;font-size:38px;color:var(--ink)}
.photo{position:absolute}
.tagline{left:122px;top:940px;font-family:"Cabin",sans-serif;font-weight:500;font-size:40px;line-height:50px}
.heading{font-family:"Cabin",sans-serif;font-weight:500;font-size:39px;line-height:46px}
.copy{font-size:15px;line-height:25.8px;color:var(--body)}
.card{top:1280px;width:311px;height:367px;background:var(--card);box-shadow:0 2px 8px rgba(0,0,0,.18);text-align:center}
.card svg{position:absolute;left:50%;top:38px;transform:translateX(-50%)}
.card h3{position:absolute;left:0;width:100%;top:130px;font-family:"Cabin",sans-serif;font-weight:500;font-size:23px;line-height:31px}
.card p{position:absolute;left:28px;width:255px;top:200px;font-size:15px;line-height:25.8px;color:var(--body)}
.card .btn{position:absolute;left:50%;transform:translateX(-50%);top:292px}
.clients{left:0;top:2572px;width:1200px;height:240px;background:var(--white);border-top:1px solid #e6e6e6}
.client{top:2680px;height:80px;display:flex;align-items:center;justify-content:center;font-family:"Cabin",sans-serif;font-weight:600;font-size:40px}
.strip{left:0;top:2812px;width:1200px;height:6px;background:#dcdcdc}
.site-footer{left:0;top:2818px;width:1200px;height:286px;background:var(--footer);color:var(--white);font-family:"Poppins",sans-serif}
.social{left:549px;top:2968px;display:flex;gap:16px}
.social span{width:27px;height:27px;border:1.5px solid var(--white);border-radius:50%}
.foot-nav{left:0;top:3018px;width:1200px;display:flex;justify-content:center;gap:30px;font-size:17px}
.foot-rule{left:113px;top:3060px;width:977px;height:1px;background:#777}
.copyright{left:0;top:3073px;width:1200px;text-align:center;font-size:13px}
</style>
</head>
<body>
<div class="page">

<header class="abs site-header">
  <div class="abs brand" style="left:118px;top:18px">
    <span class="brand-mark" role="img" aria-label="Brightwell Aero Services emblem"></span>
    <span>Brightwell Aero<br>Services</span>
  </div>
  <nav class="abs nav"><span>Home</span><span>about us</span><span>services</span><span>contact</span></nav>
</header>

<section class="abs hero" role="img" aria-label="Airliner climbing against a sunset sky"></section>
<h1 class="abs hero-title" style="left:114px;top:190px;font-family:'Cabin',sans-serif;font-weight:600;font-size:54px;line-height:52px;color:#fff">Welcome to<br>Brightwell Aero<br>services</h1>
<a class="abs btn" style="left:114px;top:373px">Read More</a>

<h2 class="abs section-title" style="top:646px">About Us</h2>
<div class="photo" role="img" aria-label="Twin turboprop aircraft parked on a runway" style="left:114px;top:714px;width:486px;height:191px;background:linear-gradient(180deg,#b9cde0 0%,#e9eef2 50%,#8f8f86 100%)"></div>
<div class="photo" role="img" aria-label="Mechanic working on an aircraft engine" style="left:600px;top:714px;width:491px;height:191px;background:linear-gradient(90deg,#6b6e70 0%,#3c3e42 50%,#9a9da0 100%)"></div>

<div class="abs tagline">Safety in<br>mind is<br>no accident</div>
<a class="abs btn" style="left:114px;top:1103px">Read More</a>

<h2 class="abs heading" style="left:493px;top:942px">Quality flying is safe flying</h2>
<p class="abs copy" style="left:494px;top:1004px;width:560px">Lorem Ipsum is simply dummy text of the printing and typesetting industry. Lorem Ipsum has been the industry's standard dummy text ever since the 1500s, when an unknown printer took a galley of type and scrambled it to make a type specimen book. It has survived not only five centuries, but also the leap into electronic typesetting, remaining essentially unchanged</p>

<h2 class="abs section-title" style="top:1197px">Services</h2>

<div class="abs card" style="left:88px">
  <svg width="76" height="76" viewBox="0 0 76 76" fill="none" stroke="#2aa8b8" stroke-width="6" stroke-linecap="round"><path d="M10 10 L62 62"/><path d="M62 14 L16 60"/><circle cx="62" cy="14" r="9"/><circle cx="14" cy="62" r="8"/></svg>
  <h3>Maintenance and<br>Repairs</h3>
  <p>Lorem Ipsum is simply dummy text of the printing and typesetting industry. Lorem Ipsum has been the industry's</p>
  <a class="btn">Read More</a>
</div>
<div class="abs card" style="left:444px">
  <svg width="100" height="70" viewBox="0 0 100 70" fill="#2aa8b8"><path d="M6 30 L80 14 L94 18 L86 24 L30 40 L10 40 Z"/><path d="M40 22 L60 6 L66 8 L56 24 Z"/><rect x="46" y="44" width="36" height="18" rx="2" fill="none" stroke="#2aa8b8" stroke-width="2"/></svg>
  <h3>Small Aircraft Rental</h3>
  <p>Lorem Ipsum is simply dummy text of the printing and typesetting industry. Lorem Ipsum has been the industry's</p>
  <a class="btn">Read More</a>
</div>
<div class="abs card" style="left:799px">
  <svg width="84" height="66" viewBox="0 0 84 66" fill="#2aa8b8"><path d="M2 30 L50 26 L56 6 L62 6 L60 26 L72 26 L72 32 L60 34 L62 56 L56 56 L50 36 L2 34 Z"/><rect x="58" y="36" width="22" height="26" fill="none" stroke="#2aa8b8" stroke-width="2"/></svg>
  <h3>Flight School</h3>
  <p>Lorem Ipsum is simply dummy text of the printing and typesetting industry. Lorem Ipsum has been the industry's</p>
  <a class="btn">Read More</a>
</div>

<div class="photo" role="img" aria-label="Pilot seated in a cockpit" style="left:114px;top:1722px;width:214px;height:169px;background:linear-gradient(135deg,#3a3f44 0%,#9aa3a8 60%,#d8d8d4 100%)"></div>
<div class="photo" role="img" aria-label="Two people beside a small aircraft" style="left:346px;top:1722px;width:214px;height:169px;background:linear-gradient(135deg,#c9d7e2 0%,#8b8e90 60%,#4a5560 100%)"></div>
<div class="photo" role="img" aria-label="Single engine aircraft on the apron" style="left:114px;top:1911px;width:446px;height:169px;background:linear-gradient(180deg,#d8dde2 0%,#eef0f2 45%,#b7b2a8 100%)"></div>
<h2 class="abs heading" style="left:603px;top:1702px">Rental and School Section</h2>
<p class="abs copy" style="left:605px;top:1781px;width:462px">Lorem Ipsum is simply dummy text of the printing and typesetting industry. Lorem Ipsum has been the industry's standard dummy text ever since the 1500s, when an unknown printer took a galley of type and scrambled it to make a type specimen book. It has survived not only five centuries, but also the leap into electronic typesetting, remaining essentially&nbsp; Lorem Ipsum is simply dummy text of the printing and typesetting industry. Lorem Ipsum has been the industry's standard dummy text ever since the 1500s, when an</p>
<a class="abs btn" style="left:603px;top:2027px">Read More</a>

<h2 class="abs heading" style="left:114px;top:2138px">Service And Maintenance</h2>
<p class="abs copy" style="left:115px;top:2200px;width:462px">Lorem Ipsum is simply dummy text of the printing and typesetting industry. Lorem Ipsum has been the industry's standard dummy text ever since the 1500s, when an unknown printer took a galley of type and scrambled it to make a type specimen book. It has survived not only five centuries, but also the leap into electronic typesetting, remaining essentially&nbsp; Lorem Ipsum is simply dummy text of the printing and typesetting industry. Lorem Ipsum has been the industry's standard dummy text ever since the 1500s, when an</p>
<a class="abs btn" style="left:113px;top:2447px">Read More</a>
<div class="photo" role="img" aria-label="Aircraft under repair inside a hangar" style="left:613px;top:2161px;width:225px;height:341px;background:linear-gradient(180deg,#3c4248 0%,#9aa0a4 50%,#6a6c6a 100%)"></div>
<div class="photo" role="img" aria-label="Hangar with several aircraft in maintenance" style="left:859px;top:2161px;width:225px;height:341px;background:linear-gradient(180deg,#3a4046 0%,#8d9296 50%,#5d5f5c 100%)"></div>

<section class="abs clients"></section>
<h2 class="abs section-title" style="top:2606px">Our Clients</h2>
<div class="abs client" style="left:130px;width:180px;color:#111">Harlan</div>
<div class="abs client" style="left:370px;width:220px;color:#c8242b">Vantorcraft</div>
<div class="abs client" style="left:670px;width:140px;color:#111;font-size:30px">Delkin</div>
<div class="abs client" style="left:920px;width:140px;color:#111;font-size:30px">Ralstead</div>
<div class="abs strip"></div>

<footer class="abs site-footer"></footer>
<div class="abs brand" style="left:413px;top:2873px">
  <span class="brand-mark" role="img" aria-label="Brightwell Aero Services emblem"></span>
  <span>Brightwell Aero<br>Services</span>
</div>
<div class="abs social" aria-label="Social links"><span></span><span></span><span></span></div>
<nav class="abs foot-nav" style="color:#fff;font-family:'Poppins',sans-serif"><span>Home</span><span>About Us</span><span>Services</span><span>Contact</span></nav>
<div class="abs foot-rule"></div>
<p class="abs copyright" style="color:#fff;font-family:'Poppins',sans-serif">2023 © brightwell aero services | All Rights Reserved</p>

</div>
</body>
</html>
```